Boutique Technology Consultancy specialising is Electronic and physical security

We need to redo our existing outdated website. For your reference the link www.pelu.com.au

```html
<!DOCTYPE html>
<html lang="en">
<head>
<meta charset="utf-8">
<title>PELU Services</title>
<link rel="stylesheet" href="https://fonts.googleapis.com/css2?family=Poppins:wght@400;500;600;700;800&display=swap">
<style>
:root{
  --red:#d42a20;
  --dark:#1c1c1c;
  --ink:#222222;
  --text:#3a3a3a;
  --grey:#f2f2f2;
  --white:#ffffff;
}
*{margin:0;padding:0;box-sizing:border-box}
html,body{width:1200px;height:4792px;overflow:hidden;background:var(--white)}
body{position:relative;font-family:"Poppins",sans-serif;color:var(--text)}
.abs{position:absolute}
.btn{position:absolute;background:var(--red);color:var(--white);font-weight:600;display:flex;align-items:center;justify-content:center;text-decoration:none}
.photo{position:absolute}
/* header */
.topline{left:0;top:0;width:1200px;height:5px;background:var(--red)}
.brand{left:75px;top:48px;display:flex;align-items:center;gap:12px;font-weight:700;font-size:56px;color:var(--ink);letter-spacing:1px;line-height:1}
.brand-dot{width:22px;height:22px;background:var(--red)}
.brand small{display:block;font-size:13px;letter-spacing:6px;font-weight:500;margin-top:4px}
.phone{left:712px;top:36px;font-size:24px;font-weight:600;color:var(--red);display:flex;align-items:center;gap:10px}
.quote{left:933px;top:25px;width:192px;height:52px;background:var(--dark);font-size:16px}
.nav{top:111px;left:460px;display:flex;gap:48px;font-size:16px;font-weight:600;color:var(--ink)}
.nav .on{color:var(--red);text-decoration:underline;text-underline-offset:6px}
/* hero */
.hero{left:0;top:155px;width:1200px;height:765px;background:linear-gradient(180deg,#b8b4ae 0%,#8d8780 50%,#a19b93 100%)}
.hero-title{left:0;top:405px;width:1200px;text-align:center;color:var(--white);font-weight:800;font-size:72px;letter-spacing:1px}
.hero-sub{left:0;top:490px;width:1200px;text-align:center;color:var(--white);font-weight:700;font-size:36px}
.hero-btn{left:531px;top:563px;width:139px;height:49px;font-size:16px}
.dots{left:484px;top:745px;display:flex;gap:10px}
.dots span{width:52px;height:6px;background:var(--white)}
.dots span.on{background:#333}
/* about */
.about-img{left:75px;top:992px;width:512px;height:458px;background:linear-gradient(135deg,#d8d4cd,#6d6a66)}
.about-box{left:553px;top:1060px;width:647px;height:468px;background:var(--grey)}
.h2{font-weight:700;font-size:40px;color:var(--ink);line-height:1.12}
.h2 .r{color:var(--red)}
.about-head{left:580px;top:1100px}
.about-text{left:580px;top:1208px;width:520px;font-size:17px;line-height:1.68}
.about-text p{margin-bottom:14px}
.about-btn{left:580px;top:1420px;width:160px;height:47px;font-size:18px}
/* services */
.services{left:0;top:1580px;width:1200px;height:820px;background:linear-gradient(180deg,#2c2c2c,#171717)}
.sec-title{left:0;width:1200px;text-align:center;font-weight:700;font-size:40px}
.svc-desc{left:150px;top:1786px;width:900px;text-align:center;color:var(--white);font-size:18px;line-height:1.6}
.card{position:absolute;background:var(--white);top:1882px;width:328px;height:354px;padding:30px 20px}
.card h3{font-size:25px;font-weight:700;color:var(--red);line-height:1.25;margin:18px 0 16px}
.card ul{list-style:none}
.card li{font-size:15px;color:var(--ink);display:flex;gap:16px;margin-bottom:14px;line-height:1.5}
.tick{flex:none;width:16px;height:16px;margin-top:3px}
/* team */
.member{position:absolute;top:2530px;width:242px;text-align:center}
.member .photo{position:relative;width:242px;height:255px;background:linear-gradient(180deg,#9a8f85,#cfc5b8 55%,#2d3340)}
.member h4{font-size:22px;font-weight:600;color:var(--ink);margin-top:10px}
.member p{font-size:16px;color:var(--red)}
.arrow{position:absolute;width:20px;height:30px}
/* experience */
.experience{left:0;top:2925px;width:1200px;height:815px;background:linear-gradient(180deg,#2a2825,#1a1816)}
.proj{position:absolute;top:3127px;width:328px;height:435px;background:var(--white);text-align:center}
.proj .photo{position:relative;width:328px;height:218px}
.proj h3{font-size:26px;font-weight:600;color:var(--ink);margin:18px 0 10px}
.proj p{font-size:15px;line-height:1.65;color:var(--text);padding:0 22px}
.proj .btn{left:82px;bottom:-20px;width:164px;height:45px;font-size:19px}
/* contact */
.contact-box{left:0;top:3870px;width:645px;height:470px;background:var(--grey)}
.contact-img{left:615px;top:3805px;width:512px;height:460px;background:linear-gradient(135deg,#e9e7e3,#a7a9a6 60%,#5a5e63)}
.contact-head{left:75px;top:3935px}
.ci{position:absolute;left:75px;display:flex;gap:24px;font-size:17px;line-height:1.55;color:var(--ink)}
.ci-icon{flex:none;width:38px;height:38px;border-radius:50%;background:var(--red)}
.contact-btn{left:75px;top:4218px;width:163px;height:47px;font-size:20px}
/* footer */
.footer{left:0;top:4400px;width:1200px;height:392px;background:#000}
.f-brand{left:0;top:4530px;width:1200px;display:flex;justify-content:center;align-items:center;gap:12px;font-weight:700;font-size:56px;color:var(--white);line-height:1}
.f-brand small{display:block;font-size:13px;letter-spacing:6px;font-weight:500;margin-top:4px}
.f-nav{left:0;top:4635px;width:1200px;display:flex;justify-content:center;gap:50px;color:var(--white);font-weight:600;font-size:17px}
.f-copy{left:0;top:4677px;width:1200px;text-align:center;color:var(--white);font-size:13px}
.f-social{left:0;top:4716px;width:1200px;display:flex;justify-content:center;gap:18px}
.f-social span{width:24px;height:24px;border-radius:50%;background:var(--white)}
</style>
</head>
<body>

<div class="abs topline"></div>
<div class="abs brand"><span class="brand-dot"></span><div>PELU<small>SERVICES</small></div></div>
<div class="abs phone">
  <svg width="20" height="20" viewBox="0 0 24 24"><path fill="#d42a20" d="M6.6 10.8a15 15 0 0 0 6.6 6.6l2.2-2.2c.3-.3.7-.4 1-.2 1.1.4 2.3.6 3.6.6.6 0 1 .4 1 1V20c0 .6-.4 1-1 1A17 17 0 0 1 3 4c0-.6.4-1 1-1h3.5c.6 0 1 .4 1 1 0 1.3.2 2.5.6 3.6.1.3 0 .7-.2 1z"/></svg>
  1300 555 014
</div>
<a class="btn quote">REQUEST A QUOTE</a>
<nav class="abs nav"><span class="on">HOME</span><span>EXPERIENCE</span><span>SERVICES</span><span>TEAM</span><span>ABOUT</span><span>CONTACT</span></nav>

<section class="abs hero" role="img" aria-label="Team meeting around a boardroom table in front of a whiteboard"></section>
<svg class="abs" style="left:0;top:780px" width="1200" height="145" viewBox="0 0 1200 145">
  <polygon fill="#ffffff" points="0,28 1200,95 1200,145 0,145"/>
  <polygon fill="#d42a20" points="0,28 600,82 0,140"/>
</svg>
<h1 class="abs hero-title">PELU SERVICES</h1>
<p class="abs hero-sub">YOUR TECHNOLOGY PROJECTS MADE EASY.</p>
<a class="btn hero-btn">READ MORE</a>
<div class="abs dots"><span class="on"></span><span></span><span></span><span></span></div>

<div class="photo about-img" role="img" aria-label="Colleagues gathered around a desk reviewing plans"></div>
<div class="abs about-box"></div>
<h2 class="abs h2 about-head">ABOUT<br><span class="r">PELU SERVICES</span></h2>
<div class="abs about-text">
  <p>PELU Services was established in 2016 by Ned Harlow to provide technology consulting services to corporate and government clients.</p>
  <p>In 2022, PELU Services merged Vantra Group into its operations, bringing increased capacity and capability to the NSW office.</p>
</div>
<a class="btn about-btn">Read More</a>

<section class="abs services" role="img" aria-label="Dark background of a consultant at work"></section>
<svg class="abs" style="left:0;top:1575px" width="1200" height="115" viewBox="0 0 1200 115">
  <polygon fill="#ffffff" points="0,0 1200,0 1200,8 0,8"/>
  <polygon fill="#ffffff" points="650,56 1200,10 1200,0 650,0"/>
  <polygon fill="#d42a20" points="650,56 1200,10 1200,105"/>
</svg>
<svg class="abs" style="left:0;top:2290px" width="1200" height="115" viewBox="0 0 1200 115">
  <polygon fill="#ffffff" points="0,10 1200,105 1200,115 0,115"/>
  <polygon fill="#d42a20" points="0,5 580,55 0,110"/>
</svg>
<h2 class="abs sec-title" style="top:1718px;color:#fff">OUR SERVICES</h2>
<p class="abs svc-desc">PELU Services provides independent professional services for projects as well as operations and maintenance. We offer end to end services including.</p>

<div class="card" style="left:75px">
  <svg width="60" height="60" viewBox="0 0 60 60"><rect x="8" y="8" width="40" height="44" fill="none" stroke="#222" stroke-width="2.5"/><path d="M16 40h24M16 30h24M16 20h14" stroke="#222" stroke-width="2.5"/></svg>
  <h3>STRATEGY</h3>
  <ul>
    <li><svg class="tick" viewBox="0 0 16 16"><circle cx="8" cy="8" r="8" fill="#d42a20"/><path d="M4.5 8.2l2.3 2.3 4.7-4.8" stroke="#fff" stroke-width="2" fill="none"/></svg>Technology roadmaps</li>
    <li><svg class="tick" viewBox="0 0 16 16"><circle cx="8" cy="8" r="8" fill="#d42a20"/><path d="M4.5 8.2l2.3 2.3 4.7-4.8" stroke="#fff" stroke-width="2" fill="none"/></svg>Master standards</li>
    <li><svg class="tick" viewBox="0 0 16 16"><circle cx="8" cy="8" r="8" fill="#d42a20"/><path d="M4.5 8.2l2.3 2.3 4.7-4.8" stroke="#fff" stroke-width="2" fill="none"/></svg>Asset management plans</li>
  </ul>
</div>
<div class="card" style="left:437px">
  <svg width="60" height="60" viewBox="0 0 60 60"><rect x="8" y="8" width="44" height="44" fill="none" stroke="#222" stroke-width="2.5"/><path d="M8 24h44M24 24v28" stroke="#222" stroke-width="2.5"/></svg>
  <h3>PROJECTS</h3>
  <ul>
    <li><svg class="tick" viewBox="0 0 16 16"><circle cx="8" cy="8" r="8" fill="#d42a20"/><path d="M4.5 8.2l2.3 2.3 4.7-4.8" stroke="#fff" stroke-width="2" fill="none"/></svg>Audit</li>
    <li><svg class="tick" viewBox="0 0 16 16"><circle cx="8" cy="8" r="8" fill="#d42a20"/><path d="M4.5 8.2l2.3 2.3 4.7-4.8" stroke="#fff" stroke-width="2" fill="none"/></svg>Design</li>
    <li><svg class="tick" viewBox="0 0 16 16"><circle cx="8" cy="8" r="8" fill="#d42a20"/><path d="M4.5 8.2l2.3 2.3 4.7-4.8" stroke="#fff" stroke-width="2" fill="none"/></svg>Procurement</li>
    <li><svg class="tick" viewBox="0 0 16 16"><circle cx="8" cy="8" r="8" fill="#d42a20"/><path d="M4.5 8.2l2.3 2.3 4.7-4.8" stroke="#fff" stroke-width="2" fill="none"/></svg>Technical project management</li>
    <li><svg class="tick" viewBox="0 0 16 16"><circle cx="8" cy="8" r="8" fill="#d42a20"/><path d="M4.5 8.2l2.3 2.3 4.7-4.8" stroke="#fff" stroke-width="2" fill="none"/></svg>Witness testing</li>
  </ul>
</div>
<div class="card" style="left:798px">
  <svg width="60" height="60" viewBox="0 0 60 60"><circle cx="30" cy="22" r="12" fill="none" stroke="#222" stroke-width="2.5"/><circle cx="18" cy="44" r="9" fill="none" stroke="#222" stroke-width="2.5"/><circle cx="42" cy="44" r="9" fill="none" stroke="#222" stroke-width="2.5"/></svg>
  <h3>OPERATIONS<br>&amp; MAINTENANCE</h3>
  <ul>
    <li><svg class="tick" viewBox="0 0 16 16"><circle cx="8" cy="8" r="8" fill="#d42a20"/><path d="M4.5 8.2l2.3 2.3 4.7-4.8" stroke="#fff" stroke-width="2" fill="none"/></svg>Service &amp; maintenance specifications</li>
    <li><svg class="tick" viewBox="0 0 16 16"><circle cx="8" cy="8" r="8" fill="#d42a20"/><path d="M4.5 8.2l2.3 2.3 4.7-4.8" stroke="#fff" stroke-width="2" fill="none"/></svg>Policies and procedures</li>
    <li><svg class="tick" viewBox="0 0 16 16"><circle cx="8" cy="8" r="8" fill="#d42a20"/><path d="M4.5 8.2l2.3 2.3 4.7-4.8" stroke="#fff" stroke-width="2" fill="none"/></svg>Procurement</li>
    <li><svg class="tick" viewBox="0 0 16 16"><circle cx="8" cy="8" r="8" fill="#d42a20"/><path d="M4.5 8.2l2.3 2.3 4.7-4.8" stroke="#fff" stroke-width="2" fill="none"/></svg>Service reviews</li>
  </ul>
</div>

<h2 class="abs sec-title h2" style="top:2448px">OUR <span class="r">TEAM</span></h2>
<svg class="arrow" style="left:42px;top:2660px" viewBox="0 0 20 30"><path d="M15 3L4 15l11 12" stroke="#222" stroke-width="2.5" fill="none"/></svg>
<svg class="arrow" style="left:1138px;top:2660px" viewBox="0 0 20 30"><path d="M5 3l11 12L5 27" stroke="#222" stroke-width="2.5" fill="none"/></svg>
<div class="member" style="left:75px"><div class="photo" role="img" aria-label="Portrait of Ned Harlow"></div><h4>Ned Harlow</h4><p>Principal Consultant</p></div>
<div class="member" style="left:345px"><div class="photo" role="img" aria-label="Portrait of Grant Pell"></div><h4>Grant Pell</h4><p>Principal Consultant</p></div>
<div class="member" style="left:615px"><div class="photo" role="img" aria-label="Portrait of Owen Trask"></div><h4>Owen Trask</h4><p>Senior Consultant</p></div>
<div class="member" style="left:885px"><div class="photo" role="img" aria-label="Portrait of Liam Corrie"></div><h4>Liam Corrie</h4><p>Senior Consultant</p></div>

<section class="abs experience" role="img" aria-label="Dark aerial city skyline at dusk"></section>
<svg class="abs" style="left:0;top:2920px" width="1200" height="115" viewBox="0 0 1200 115">
  <polygon fill="#ffffff" points="0,0 1200,0 1200,8 0,8"/>
  <polygon fill="#ffffff" points="650,56 1200,10 1200,0 650,0"/>
  <polygon fill="#d42a20" points="650,56 1200,10 1200,105"/>
</svg>
<svg class="abs" style="left:0;top:3630px" width="1200" height="115" viewBox="0 0 1200 115">
  <polygon fill="#ffffff" points="0,10 1200,105 1200,115 0,115"/>
  <polygon fill="#d42a20" points="0,5 580,55 0,110"/>
</svg>
<h2 class="abs sec-title" style="top:3042px;color:#fff">EXPERIENCE</h2>
<svg class="arrow" style="left:42px;top:3330px" viewBox="0 0 20 30"><path d="M15 3L4 15l11 12" stroke="#fff" stroke-width="2.5" fill="none"/></svg>
<svg class="arrow" style="left:1138px;top:3330px" viewBox="0 0 20 30"><path d="M5 3l11 12L5 27" stroke="#fff" stroke-width="2.5" fill="none"/></svg>
<div class="proj" style="left:75px"><div class="photo" style="background:linear-gradient(180deg,#c9c1b5,#a0562f 60%,#6d5846)" role="img" aria-label="Brick tower under a glass dome"></div><h3>Harbourline Central</h3><p>Security technology design consulting for this popular retail and entertainment hub which is managed by the Marlow Group.</p><a class="btn">Read More</a></div>
<div class="proj" style="left:437px"><div class="photo" style="background:linear-gradient(180deg,#7fa9cf,#c3d6e4 55%,#7b8a6a)" role="img" aria-label="Highway lined with power transmission towers"></div><h3>RidgeWay</h3><p>Virtual servers, network and CCTV upgrade design and project management for this landmark road transportation PPP.</p><a class="btn">Read More</a></div>
<div class="proj" style="left:798px"><div class="photo" style="background:linear-gradient(180deg,#8c9498,#c9ccc9 60%,#6f7477)" role="img" aria-label="Glass office tower against a cloudy sky"></div><h3>Corvel Tower</h3><p>Shared building network and security systems integration consulting for this iconic office tower which is managed by Kestrel Property.</p><a class="btn">Read More</a></div>

<div class="abs contact-box"></div>
<div class="photo contact-img" role="img" aria-label="Three colleagues smiling while looking at a tablet"></div>
<h2 class="abs h2 contact-head">CONTACT <span class="r">US</span></h2>
<div class="ci" style="top:4012px"><span class="ci-icon"></span><span>Level 3, 118 Elder Street Melbourne, Vic,<br>3000 Australia</span></div>
<div class="ci" style="top:4080px"><span class="ci-icon"></span><span style="padding-top:6px">1300 555 014</span></div>
<div class="ci" style="top:4139px"><span class="ci-icon"></span><span style="padding-top:6px">info@pelu.com.au</span></div>
<a class="btn contact-btn">Contact Us</a>

<footer class="abs footer"></footer>
<svg class="abs" style="left:0;top:4395px" width="1200" height="120" viewBox="0 0 1200 120">
  <polygon fill="#ffffff" points="0,0 1200,0 1200,10 0,10"/>
  <polygon fill="#ffffff" points="650,56 1200,12 1200,0 650,0"/>
  <polygon fill="#d42a20" points="650,56 1200,12 1200,105"/>
</svg>
<div class="abs f-brand"><span class="brand-dot"></span><div>PELU<small>SERVICES</small></div></div>
<nav class="abs f-nav"><span>HOME</span><span>EXPERIENCE</span><span>SERVICES</span><span>TEAM</span><span>ABOUT</span><span>CONTACT</span></nav>
<p class="abs f-copy">Company © 2023 Company Name All Right Reserved</p>
<div class="abs f-social" aria-label="Social links"><span></span><span></span><span></span><span></span><span></span></div>

</body>
</html>
```